Boutique Store Selling Antiques and Unique Finds

I need a Web Page designed for my Store Called "Willow Lane". I would like a very classic, muted design that looks European when pulled up. I will be selling Antiques from all over the world and Unique finds that have reproduced. I will also be selling high-end purses and jewelry with unique, reasonable products for the every-day buyer as well.

Target Market(s)

25-70 year old men and women;)

Coding

Coded - Design and coding required

Number of Pages Required

1 page

Colors

Designer to choose only greyscale colors for use in the design.

Requirements
Must have
• I want it

```html
<!DOCTYPE html>
<html lang="en">
<head>
<meta charset="utf-8">
<title>Willow Lane — Antiques &amp; Unique Finds</title>
<link href="https://fonts.googleapis.com/css2?family=Lora:ital,wght@0,400;0,500;1,400&family=Open+Sans:wght@400;600&display=swap" rel="stylesheet">
<style>
:root{
  --ink:#0b0b0e;
  --ink-soft:#1a1a1d;
  --paper:#ffffff;
  --text:#2a2a2a;
  --muted:#9a9a9a;
  --hero-a:#6e4a33;
  --hero-b:#a67a56;
  --hero-c:#3b2418;
  --shop-a:#141416;
  --shop-b:#26262a;
}
*{margin:0;padding:0;box-sizing:border-box}
html,body{width:1200px;height:2286px;overflow:hidden;background:var(--paper)}
body{position:relative;font-family:"Open Sans",Arial,sans-serif;color:var(--text)}
.abs{position:absolute}
.serif{font-family:"Lora",Georgia,serif}

/* header */
.site-header{left:0;top:0;width:1200px;height:98px;background:var(--paper)}
.brand{left:144px;top:44px;font-family:"Lora",Georgia,serif;font-size:27px;letter-spacing:5px;text-transform:uppercase;color:var(--ink);font-weight:500}
.nav{left:439px;top:63px;display:flex;gap:0;font-family:"Lora",Georgia,serif;font-size:13.5px;color:var(--ink);text-transform:uppercase}
.nav a{position:absolute;white-space:nowrap;color:var(--ink);text-decoration:none}
.nav a.current{text-decoration:underline;text-underline-offset:3px}
.header-icons{left:925px;top:18px}

/* hero */
.hero{left:0;top:98px;width:1200px;height:516px;background:radial-gradient(ellipse at 72% 55%,var(--hero-b) 0%,var(--hero-a) 40%,var(--hero-c) 100%)}
.hero-title{left:144px;top:116px;font-family:"Lora",Georgia,serif;font-style:italic;font-size:41px;line-height:49px;color:#fff;text-transform:uppercase}
.btn-ghost-light{left:144px;top:223px;width:128px;height:44px;border:1px solid #fff;color:#fff;font-family:"Lora",Georgia,serif;font-size:15px;display:flex;align-items:center;justify-content:center}
.arrow-box{width:40px;height:40px;background:var(--ink);display:flex;align-items:center;justify-content:center}

/* dividers */
.divider{left:0;width:1200px;height:70px}

/* welcome */
.section-title{width:1200px;left:0;text-align:center;font-family:"Lora",Georgia,serif;font-size:33px;color:var(--ink);text-transform:uppercase}
.welcome-text{left:144px;top:784px;width:912px;text-align:center;font-size:13.6px;line-height:27px;color:#333}
.btn-ghost-dark{left:540px;top:907px;width:120px;height:43px;border:1px solid var(--ink);color:var(--ink);font-family:"Lora",Georgia,serif;font-size:15px;display:flex;align-items:center;justify-content:center}

/* shop */
.shop{left:0;top:1030px;width:1200px;height:516px;background:radial-gradient(ellipse at 60% 60%,var(--shop-b) 0%,var(--shop-a) 75%)}
.shop-card{top:1173px;width:297px}
.shop-card .photo{width:297px;height:240px}
.shop-card .label{margin-top:6px;text-align:center;font-family:"Lora",Georgia,serif;font-size:21px;color:#fff}

/* newsletter */
.newsletter-sub{left:0;width:1200px;top:1711px;text-align:center;font-size:13.6px;color:#333}
.signup{left:404px;top:1744px;width:392px;height:48px;border:1px solid var(--ink);background:#fff}
.signup .field{position:absolute;left:17px;top:14px;font-size:14px;color:#333}
.signup .submit{position:absolute;right:2px;top:2px;width:119px;height:42px;background:var(--ink);color:#fff;font-family:"Lora",Georgia,serif;font-size:15px;display:flex;align-items:center;justify-content:center}

/* footer */
.site-footer{left:0;top:1923px;width:1200px;height:363px;background:var(--ink)}
.footer-heading{top:1990px;font-family:"Lora",Georgia,serif;font-size:20px;color:#fff;text-transform:uppercase;white-space:nowrap}
.footer-list{top:2034px;list-style:none;font-size:12px;color:var(--muted);line-height:29px}
.contact-list li{display:flex;align-items:center;gap:13px}
.contact-list svg{flex:none}
.footer-rule{left:144px;top:2214px;width:912px;height:1px;background:#2e2e32}
.copyright{left:0;width:1200px;top:2241px;text-align:center;font-size:12px;color:var(--muted)}
</style>
</head>
<body>

<header class="site-header abs">
  <div class="brand abs">Willow Lane</div>
  <nav class="nav abs">
    <a class="current" style="left:0">New Arrivals</a>
    <a style="left:126px">Purses</a>
    <a style="left:207px">Jewelry</a>
    <a style="left:298px">Gifts</a>
    <a style="left:368px">Discounts</a>
    <a style="left:476px">About</a>
    <a style="left:554px">Contact</a>
  </nav>
  <svg class="header-icons abs" width="135" height="30" viewBox="0 0 135 30" aria-label="Search, account and cart">
    <circle cx="14" cy="13" r="6.5" fill="none" stroke="#0b0b0e" stroke-width="3"/>
    <line x1="19" y1="18" x2="24" y2="23" stroke="#0b0b0e" stroke-width="3.5" stroke-linecap="round"/>
    <circle cx="72" cy="10" r="5.5" fill="#0b0b0e"/>
    <path d="M62 24 q10 -12 20 0 z" fill="#0b0b0e"/>
    <circle cx="107" cy="8" r="8" fill="#bdbdbd"/>
    <text x="107" y="11" font-size="8" text-anchor="middle" fill="#333" font-family="Open Sans,sans-serif">0</text>
    <path d="M112 12 h4 l2 8 h10 l2 -6 h-13" fill="none" stroke="#0b0b0e" stroke-width="2.2"/>
    <rect x="118" y="14" width="11" height="5" fill="#0b0b0e"/>
    <circle cx="120" cy="23.5" r="1.8" fill="#0b0b0e"/>
    <circle cx="127" cy="23.5" r="1.8" fill="#0b0b0e"/>
  </svg>
</header>

<section class="hero abs" role="img" aria-label="Photograph of antique brass compass, telescope and wooden chest in warm light"></section>
<h1 class="hero-title abs" style="top:214px">Nulla tristique<br>posuere molestie</h1>
<div class="btn-ghost-light abs" style="top:321px">READ MORE</div>
<div class="arrow-box abs" style="left:51px;top:337px">
  <svg width="14" height="22" viewBox="0 0 14 22"><path d="M11 3 L4 11 L11 19" fill="none" stroke="#fff" stroke-width="3"/></svg>
</div>
<div class="arrow-box abs" style="left:1107px;top:337px">
  <svg width="14" height="22" viewBox="0 0 14 22"><path d="M3 3 L10 11 L3 19" fill="none" stroke="#fff" stroke-width="3"/></svg>
</div>

<svg class="divider abs" style="top:596px" width="1200" height="66" viewBox="0 0 1200 66" aria-hidden="true">
  <rect x="0" y="27" width="1200" height="16" fill="#0b0b0e"/>
  <ellipse cx="600" cy="34" rx="18" ry="29" fill="#0b0b0e" stroke="#fff" stroke-width="4"/>
</svg>

<h2 class="section-title abs" style="top:730px">Welcome to Willow Lane</h2>
<p class="welcome-text abs">Aliquam erat volutpat. Etiam quis aliquet risus. Duis ornare erat eget magna dapibus, in accumsan quam pharetra. Nam tempus, quam in bibendum vulputate, sapien dolor viverra nisl, vitae euismod elit turpis et nulla. Aliquam erat volutpat. Pellentesque blandit lacus eget nunc faucibus, et tincidunt eros viverra. Phasellus consequat sagittis nisi suscipit feugiat. Cras eget leo sed nunc hendrerit ultricies eu at nisl. Praesent iaculis faucibus urna sit amet lacinia. Maecenas consequat justo enim, ac mattis massa imperdiet quis. Fusce eget neque elit.</p>
<div class="btn-ghost-dark abs">READ MORE</div>

<section class="shop abs" role="img" aria-label="Dark photograph of a vintage typewriter and gauges"></section>
<h2 class="section-title abs" style="top:1107px;color:#fff">Shop</h2>
<svg class="abs" style="left:54px;top:1278px" width="22" height="30" viewBox="0 0 22 30" aria-hidden="true"><path d="M16 3 L5 15 L16 27" fill="none" stroke="#fff" stroke-width="4"/></svg>
<svg class="abs" style="left:1123px;top:1278px" width="22" height="30" viewBox="0 0 22 30" aria-hidden="true"><path d="M6 3 L17 15 L6 27" fill="none" stroke="#fff" stroke-width="4"/></svg>

<article class="shop-card abs" style="left:144px">
  <div class="photo" role="img" aria-label="Gilded star crown resting on old leather books" style="background:linear-gradient(180deg,#c9b79c 0%,#8a6a3e 55%,#3a2a1c 100%)"></div>
  <div class="label">Large Crown</div>
</article>
<article class="shop-card abs" style="left:451px">
  <div class="photo" role="img" aria-label="Ornate jewelled crown on a pedestal in a display case" style="background:linear-gradient(180deg,#6b5530 0%,#d8d2c4 35%,#8a6f4e 70%,#2a2724 100%)"></div>
  <div class="label">Sed augue</div>
</article>
<article class="shop-card abs" style="left:758px">
  <div class="photo" role="img" aria-label="Bronze crown set with coloured stones" style="background:linear-gradient(180deg,#d6cdbd 0%,#7a5e36 50%,#3a2c1c 100%)"></div>
  <div class="label">Proin eget</div>
</article>

<svg class="divider abs" style="top:1528px" width="1200" height="66" viewBox="0 0 1200 66" aria-hidden="true">
  <rect x="0" y="27" width="1200" height="16" fill="#0b0b0e"/>
  <ellipse cx="600" cy="32" rx="18" ry="29" fill="#0b0b0e" stroke="#fff" stroke-width="4"/>
</svg>

<h2 class="section-title abs" style="top:1669px">Newsletter Signup</h2>
<p class="newsletter-sub abs">Maecenas vel tortor accumsan quam varius imperdiet vel eget elit</p>
<div class="signup abs">
  <span class="field">Email Address</span>
  <span class="submit">SUBSCRIBE</span>
</div>

<footer class="site-footer abs"></footer>
<svg class="divider abs" style="top:1876px" width="1200" height="66" viewBox="0 0 1200 66" aria-hidden="true">
  <rect x="0" y="22" width="1200" height="16" fill="#0b0b0e"/>
  <ellipse cx="600" cy="32" rx="18" ry="29" fill="#0b0b0e" stroke="#fff" stroke-width="4"/>
</svg>

<h3 class="footer-heading abs" style="left:144px">Quick Links</h3>
<ul class="footer-list abs" style="left:144px">
  <li>Home</li><li>New Arrivals</li><li>Purses</li><li>Jewelry</li><li>Gifts</li>
</ul>
<ul class="footer-list abs" style="left:238px">
  <li>Discounts</li><li>About</li><li>Contact</li>
</ul>

<h3 class="footer-heading abs" style="left:376px">My Account</h3>
<ul class="footer-list abs" style="left:376px">
  <li>My Cart</li><li>Wishlist</li><li>Checkout</li><li>Shipping</li><li>Returns</li>
</ul>

<h3 class="footer-heading abs" style="left:584px">Contact Info</h3>
<ul class="footer-list contact-list abs" style="left:584px">
  <li><svg width="9" height="12" viewBox="0 0 9 12"><path d="M4.5 0 a4.5 4.5 0 0 1 4.5 4.5 c0 3 -4.5 7.5 -4.5 7.5 s-4.5 -4.5 -4.5 -7.5 a4.5 4.5 0 0 1 4.5 -4.5z" fill="#9a9a9a"/><circle cx="4.5" cy="4.5" r="1.6" fill="#0b0b0e"/></svg>24 Building name, Street name, City Zipcode</li>
  <li><svg width="9" height="12" viewBox="0 0 10 10"><path d="M2 0 l2 2.5 -1 1.5 q1 2 3 3 l1.5 -1 2.5 2 -1.5 2 q-5 -1 -8.5 -8.5z" fill="#9a9a9a"/></svg>Phone : 555 014 2790</li>
  <li><svg width="11" height="12" viewBox="0 0 11 8"><rect width="11" height="8" fill="#9a9a9a"/><path d="M0 0 L5.5 4.5 L11 0" fill="none" stroke="#0b0b0e" stroke-width="1"/></svg>Email : hello@willowlane-shop.com</li>
</ul>

<h3 class="footer-heading abs" style="left:909px">Follow Us On</h3>
<svg class="abs" style="left:908px;top:2039px" width="150" height="44" viewBox="0 0 150 44" aria-label="Social media links">
  <circle cx="21" cy="22" r="20" fill="none" stroke="#6a6a6e" stroke-width="1"/>
  <circle cx="73" cy="22" r="20" fill="none" stroke="#6a6a6e" stroke-width="1"/>
  <circle cx="125" cy="22" r="20" fill="none" stroke="#6a6a6e" stroke-width="1"/>
</svg>

<div class="footer-rule abs"></div>
<p class="copyright abs">Copyright &copy; 2021 &nbsp;Willow Lane. &nbsp;All rights reserved.</p>

</body>
</html>
```